Brindle Sky Port needs a new upscale business card design for our high end aircraft hangar complex

Brindle Sky Port (BSP) is a large, upscale jet hangar complex in the US housing expensive aircraft. We need a new business card design, using our current logo. We will be attending a industry convention and need a card design that will stand out and be remembered by aircraft owners and private pilots.

Target Market(s)

Aircraft pilots or owners looking for a new upscale hangar

Industry/Entity Type

Airport

Contact Information for Business Card

I like to use very heavy card stock, 400#, double sided. Square, no rounded edges please.

Colors
3276b5
0255a3
85abd2

Requirements
Must have
• An expensive, classy design, vivid colors.
Nice to have
• Needs to look very expensive and classy, and have some "pop". Designer must be able to download or copy my current typeface or fonts.
• One card side might be black with the "Logo and Brindle Sky Port Double line image in blue (or try gold, or glossy black), and perhaps have a grayed out "K720 jet silhouette". The other card side would have our contact info, and perhaps the "BSP Logo only". I'd like my contact info 'stacked', not in a paragraph format.
Should not have
• Should not look "too busy". Having a double-sided card will help.

```html
<!DOCTYPE html>
<html lang="en">
<head>
<meta charset="utf-8">
<title>Brindle Sky Port – Business Card</title>
<link href="https://fonts.googleapis.com/css2?family=Open+Sans:wght@400;600;700&display=swap" rel="stylesheet">
<style>
  :root {
    --backdrop: #2a2a2c;
    --card: #0f0f10;
    --card-panel: #141415;
    --blue-mid: #3276b5;
    --blue-deep: #0255a3;
    --blue-light: #85abd2;
    --text-light: #e6e6e6;
    --divider: #262628;
  }
  * { box-sizing: border-box; margin: 0; padding: 0; }
  html, body {
    width: 1200px; height: 900px; overflow: hidden;
    background: var(--backdrop);
    font-family: "Open Sans", Arial, sans-serif;
  }
  .sheet {
    position: relative; width: 1200px; height: 900px;
    display: flex; align-items: center; justify-content: center; gap: 40px;
  }
  .card {
    position: relative; width: 540px; height: 310px;
    background: var(--card); border-radius: 0; overflow: hidden;
    box-shadow: 0 14px 30px rgba(0,0,0,.45);
  }
  /* contact side */
  .card-contact .brand-zone {
    position: absolute; left: 0; top: 0; width: 270px; height: 100%;
    display: flex; align-items: center; justify-content: center;
  }
  .card-contact .details {
    position: absolute; left: 270px; top: 0; width: 270px; height: 100%;
    background: var(--card-panel); border-left: 1px solid var(--divider);
    padding: 58px 0 0 26px; color: var(--text-light);
  }
  .brand-mark {
    display: flex; align-items: center; gap: 12px;
    font-weight: 700; color: var(--blue-mid); letter-spacing: 2px;
  }
  .brand-mark .dot {
    width: 14px; height: 14px; border-radius: 50%; background: var(--blue-mid);
  }
  .brand-zone .brand-mark { font-size: 62px; }
  .person-name { font-size: 19px; font-weight: 600; color: var(--blue-light); line-height: 1.1; }
  .person-role { font-size: 13px; margin-top: 3px; }
  .address { font-size: 13px; line-height: 1.35; margin-top: 14px; }
  .contact-list { list-style: none; margin-top: 18px; font-size: 13px; }
  .contact-list li { display: flex; align-items: center; gap: 10px; line-height: 1.55; }
  .contact-list svg { width: 11px; height: 11px; fill: var(--blue-mid); flex: none; }
  /* logo side */
  .card-logo {
    display: flex; flex-direction: column; align-items: center; justify-content: center;
  }
  .card-logo .brand-mark { font-size: 70px; }
  .brand-name {
    margin-top: 6px; font-size: 15px; font-weight: 700; color: var(--blue-mid);
    letter-spacing: 4px; text-transform: uppercase;
  }
</style>
</head>
<body>
<main class="sheet">
  <section class="card card-contact" aria-label="Business card, contact side">
    <div class="brand-zone">
      <div class="brand-mark"><span class="dot"></span>BSP</div>
    </div>
    <div class="details">
      <p class="person-name">Elliot Harlow</p>
      <p class="person-role">Managing Director</p>
      <p class="address">4870, Hangar Row Drive<br>Country Name, 482910.</p>
      <ul class="contact-list">
        <li><svg viewBox="0 0 12 12"><path d="M2.5 0.5l2 2.5-1.2 1.2c.7 1.6 2 2.9 3.5 3.5L8 6.5l2.5 2-1.2 2.5C4.8 10.7 1.3 7.2 1 2.7z"/></svg>(044)-555-0182</li>
        <li><svg viewBox="0 0 12 12"><path d="M3 0h6v12H3zM4 1.5v7.5h4V1.5z"/></svg>123-555-0147</li>
        <li><svg viewBox="0 0 12 12"><path d="M0 2h12v8H0zM1 3l5 3.5L11 3v-.2H1z"/></svg>info@brindleskyport.com</li>
        <li><svg viewBox="0 0 12 12"><circle cx="6" cy="6" r="6"/></svg>www.brindleskyport.com</li>
      </ul>
    </div>
  </section>

  <section class="card card-logo" aria-label="Business card, logo side">
    <div class="brand-mark"><span class="dot"></span>BSP</div>
    <p class="brand-name">Brindle Sky Port.</p>
  </section>
</main>
</body>
</html>
```